Website Design for Architecture Practice

I need a home page and one sidebar/content page for an Architecture practice delivered in PSD.

This archictecture practice specialises in one-off, high end homes and commercial properties (restaurant) heavily influenced by Edmund Harcourt Vale, particularly his work on the Pellworth Museum

I am looking for a home page, and a generic content page where we can outline our services, and showcase our homes.

http://journals.kestrelhill.edu.au/artnotes/Pellworth%20Quayside%202.jpg

Target Market(s)

30-70yr old (typically wealthy) property buyers, developers and investors

Industry/Entity Type

Architecture

Number of Pages Required

2 page

Font styles to use
Serif
Sans Serif

Requirements
Must have
• Home page design
• a Content Page design (ie, top nav with sidebar)
Nice to have
• Use any Edmund Harcourt Vale images you can find via google etc as placeholders for our own photography (ie they don't need to be licensed as we will be replacing with our own commissioned photography). Full color preferred but feel free to experiment with treating any images as you see fit.

```html
<!DOCTYPE html>
<html lang="en">
<head>
<meta charset="utf-8">
<title>Halden Crest Studio</title>
<link href="https://fonts.googleapis.com/css2?family=Marcellus&family=Open+Sans:wght@400;600&display=swap" rel="stylesheet">
<style>
:root{
  --red:#c41f2c;
  --ink:#3a3a3a;
  --muted:#6f6f6f;
  --paper:#ffffff;
  --footer:#2c2c2c;
  --footer-deep:#1d1d1d;
  --footer-text:#a9a9a9;
}
*{box-sizing:border-box;margin:0;padding:0}
html,body{width:736px;height:1200px;overflow:hidden;background:var(--paper)}
body{font-family:"Open Sans",Arial,sans-serif;color:var(--ink);position:relative}

/* header */
.site-header{position:absolute;top:0;left:0;width:736px;height:50px;background:var(--paper)}
.brand{position:absolute;left:108px;top:12px;display:flex;align-items:center;gap:8px}
.brand-mark{width:24px;height:24px;background:var(--red);flex:none}
.brand-name{font-family:"Marcellus",Georgia,serif;color:var(--red);font-size:19px;line-height:1}
.header-phone{position:absolute;right:58px;top:8px;font-size:9px;color:var(--muted);display:flex;align-items:center;gap:4px}
.main-nav{position:absolute;right:58px;top:26px;display:flex;gap:2px}
.main-nav a{font-size:8px;text-transform:uppercase;color:var(--muted);text-decoration:none;padding:4px 8px;letter-spacing:.5px}
.main-nav a.active{background:#4a4a4a;color:#fff}

/* hero */
.hero{position:absolute;top:50px;left:0;width:736px;height:350px;
  background:linear-gradient(180deg,#4f6b3c 0%,#6f8a52 30%,#8c8a70 55%,#5b5a48 75%,#33402a 100%)}
.hero-caption{position:absolute;left:0;right:0;top:290px;text-align:center;color:#e1434c;font-size:14px;line-height:18px;
  font-family:"Marcellus",Georgia,serif;text-shadow:0 1px 2px rgba(0,0,0,.6)}
.hero-dots{position:absolute;left:0;right:0;top:333px;display:flex;justify-content:center;gap:6px}
.hero-dots span{width:7px;height:7px;border-radius:50%;background:#fff;opacity:.6}
.hero-dots span.on{opacity:1;background:var(--red)}

/* welcome */
.welcome{position:absolute;top:400px;left:0;width:736px;height:250px;background:var(--paper)}
.welcome-title{position:absolute;left:108px;top:30px;display:flex;align-items:center;gap:10px}
.welcome-title .brand-mark{width:32px;height:32px}
.welcome-title h1{font-family:"Marcellus",Georgia,serif;font-weight:400;font-size:19px;line-height:21px;color:var(--ink)}
.welcome-title h1 span{color:var(--red);display:block}
.welcome-text{position:absolute;left:100px;top:82px;width:300px;font-size:7.5px;line-height:13px;color:var(--muted)}
.btn{position:absolute;left:100px;top:194px;background:var(--red);color:#fff;font-size:7px;padding:4px 9px;border-radius:2px;text-decoration:none}
.photo-circle{position:absolute;border-radius:50%;border:4px solid #fff;box-shadow:0 2px 8px rgba(0,0,0,.3)}
.pc-a{left:418px;top:18px;width:134px;height:134px;background:linear-gradient(160deg,#a7c4d8,#d9d4c0 55%,#6a7a5a)}
.pc-b{left:498px;top:96px;width:122px;height:122px;background:linear-gradient(160deg,#8fb3d6,#c9a36b 60%,#7a6a4a)}
.pc-c{left:420px;top:152px;width:70px;height:70px;background:linear-gradient(160deg,#6a7f4d,#9b6c47)}

/* services band */
.services{position:absolute;top:650px;left:0;width:736px;height:233px;background:var(--red);color:#fff}
.service{position:absolute;top:28px;width:170px;text-align:center}
.service:nth-child(1){left:92px}
.service:nth-child(2){left:278px}
.service:nth-child(3){left:468px}
.service-icon{width:58px;height:58px;margin:0 auto;border:2px solid #fff;border-radius:50%;display:flex;align-items:center;justify-content:center}
.service h2{font-family:"Marcellus",Georgia,serif;font-weight:400;font-size:15px;margin-top:12px}
.service p{font-size:7.5px;line-height:12px;margin-top:7px;opacity:.9}
.service .dot{width:9px;height:9px;background:#fff;border-radius:50%;margin:16px auto 0}

/* facilities + gallery */
.info{position:absolute;top:883px;left:0;width:736px;height:177px;background:var(--paper)}
.info h3{font-family:"Marcellus",Georgia,serif;font-weight:400;font-size:16px;color:var(--ink)}
.facilities{position:absolute;left:98px;top:32px}
.facilities ul{list-style:none;margin-top:8px}
.facilities li{font-size:7.5px;color:var(--muted);line-height:16px;display:flex;align-items:center;gap:5px}
.gallery{position:absolute;left:276px;top:32px}
.gallery-row{display:flex;gap:12px;margin-top:10px}
.gallery-row div{width:112px;height:76px}
.g1{background:linear-gradient(160deg,#6c7a4a,#8c5a3a 60%,#3f3a2a)}
.g2{background:linear-gradient(160deg,#4f6a3a,#a99a7a 55%,#3a4a2e)}
.g3{background:linear-gradient(160deg,#8a5a3a,#c99a6a 55%,#5a3a2a)}

/* footer */
.site-footer{position:absolute;top:1060px;left:0;width:736px;height:122px;background:var(--footer);color:var(--footer-text)}
.footer-col{position:absolute;top:12px}
.footer-col h4{font-size:7px;font-weight:600;text-transform:uppercase;color:#ddd;letter-spacing:.6px;margin-bottom:8px}
.footer-col ul{list-style:none}
.footer-col li{font-size:7px;line-height:14px;display:flex;align-items:center;gap:5px}
.fc-links{left:104px}
.fc-contact{left:236px}
.fc-map{left:398px}
.fc-follow{left:560px}
.map{width:100px;height:62px;background:linear-gradient(135deg,#d9d6cc,#c4d0b8 55%,#b9c6d4)}
.social-square{width:11px;height:11px;background:#555;display:inline-block}
.copyright{position:absolute;top:1182px;left:0;width:736px;height:18px;background:var(--footer-deep);color:#8a8a8a;font-size:7px;text-align:center;line-height:18px}
</style>
</head>
<body>

<header class="site-header">
  <div class="brand"><span class="brand-mark"></span><span class="brand-name">Halden Crest Studio</span></div>
  <div class="header-phone">
    <svg width="9" height="9" viewBox="0 0 24 24"><path fill="#c41f2c" d="M6.6 10.8a15 15 0 0 0 6.6 6.6l2.2-2.2c.3-.3.7-.4 1-.2 1.1.4 2.3.6 3.6.6.6 0 1 .4 1 1V20c0 .6-.4 1-1 1A17 17 0 0 1 3 4c0-.6.4-1 1-1h3.5c.6 0 1 .4 1 1 0 1.3.2 2.5.6 3.6.1.3 0 .7-.2 1z"/></svg>
    555-014-7720
  </div>
  <nav class="main-nav">
    <a class="active" href="#">Home</a><a href="#">About</a><a href="#">Services</a><a href="#">Gallery</a><a href="#">Contact</a>
  </nav>
</header>

<section class="hero" role="img" aria-label="Photograph of a cantilevered stone and concrete house among forest trees">
  <p class="hero-caption">We Are An Architecture Business / Practice That Specialises In One-Off,<br>High End Homes And Commercial Properties</p>
  <div class="hero-dots"><span></span><span class="on"></span><span></span></div>
</section>

<section class="welcome">
  <div class="welcome-title"><span class="brand-mark"></span><h1>Welcome to<span>Halden Crest Studio</span></h1></div>
  <p class="welcome-text">Our studio designs considered homes and restaurants shaped by landscape, light and honest materials. Every project begins with the site, its views and the way its owners want to live, then grows into a building that belongs there. We work closely with each client from first sketch to final handover, keeping craft, structure and setting in balance so that every room feels calm, open and connected to the ground around it, season after season.</p>
  <a class="btn" href="#">Read More</a>
  <div class="photo-circle pc-a" role="img" aria-label="Photograph of a modernist house with terraces"></div>
  <div class="photo-circle pc-b" role="img" aria-label="Photograph of a house beside a pool under blue sky"></div>
  <div class="photo-circle pc-c" role="img" aria-label="Photograph of a brick house among trees"></div>
</section>

<section class="services">
  <div class="service">
    <div class="service-icon"><svg width="30" height="26" viewBox="0 0 30 26" fill="none" stroke="#fff" stroke-width="2"><path d="M3 12 15 3l12 9"/><path d="M6 10v13h18V10"/><rect x="12" y="15" width="6" height="8"/></svg></div>
    <h2>One Off</h2>
    <p>Bespoke single residences drawn from scratch for one client and one site.</p>
    <div class="dot"></div>
  </div>
  <div class="service">
    <div class="service-icon"><svg width="32" height="26" viewBox="0 0 32 26" fill="none" stroke="#fff" stroke-width="2"><path d="M2 9h28"/><path d="M5 9v14h22V9"/><path d="M8 3h16v6"/><rect x="13" y="14" width="6" height="9"/></svg></div>
    <h2>High End Homes</h2>
    <p>Luxury homes with cantilevered terraces, stone cores and open plans.</p>
    <div class="dot"></div>
  </div>
  <div class="service">
    <div class="service-icon"><svg width="28" height="28" viewBox="0 0 28 28" fill="none" stroke="#fff" stroke-width="2"><rect x="4" y="3" width="9" height="22"/><rect x="15" y="9" width="9" height="16"/><path d="M7 8h3M7 13h3M7 18h3M18 14h3M18 19h3"/></svg></div>
    <h2>Commercial Properties</h2>
    <p>Restaurants and venues designed around warm light and long views.</p>
    <div class="dot"></div>
  </div>
</section>

<section class="info">
  <div class="facilities">
    <h3>Our Facilities</h3>
    <ul>
      <li><svg width="8" height="8" viewBox="0 0 10 10"><path d="M1 5l3 3 5-6" stroke="#c41f2c" stroke-width="2" fill="none"/></svg>Site surveys and feasibility studies</li>
      <li><svg width="8" height="8" viewBox="0 0 10 10"><path d="M1 5l3 3 5-6" stroke="#c41f2c" stroke-width="2" fill="none"/></svg>Concept and detailed design</li>
      <li><svg width="8" height="8" viewBox="0 0 10 10"><path d="M1 5l3 3 5-6" stroke="#c41f2c" stroke-width="2" fill="none"/></svg>Planning and consent applications</li>
      <li><svg width="8" height="8" viewBox="0 0 10 10"><path d="M1 5l3 3 5-6" stroke="#c41f2c" stroke-width="2" fill="none"/></svg>Interior and landscape coordination</li>
      <li><svg width="8" height="8" viewBox="0 0 10 10"><path d="M1 5l3 3 5-6" stroke="#c41f2c" stroke-width="2" fill="none"/></svg>Construction oversight and handover</li>
    </ul>
  </div>
  <div class="gallery">
    <h3>Our Gallery</h3>
    <div class="gallery-row">
      <div class="g1" role="img" aria-label="Photograph of a timber house with low roofs"></div>
      <div class="g2" role="img" aria-label="Photograph of a house above a waterfall in woodland"></div>
      <div class="g3" role="img" aria-label="Photograph of a warm wood-panelled interior"></div>
    </div>
  </div>
</section>

<footer class="site-footer">
  <div class="footer-col fc-links">
    <h4>Quick Links</h4>
    <ul><li>Home</li><li>About</li><li>Services</li><li>Gallery</li><li>Contact</li></ul>
  </div>
  <div class="footer-col fc-contact">
    <h4>Contact Information</h4>
    <ul>
      <li><svg width="8" height="9" viewBox="0 0 24 24"><path fill="#a9a9a9" d="M12 2a7 7 0 0 0-7 7c0 5 7 13 7 13s7-8 7-13a7 7 0 0 0-7-7zm0 9.5A2.5 2.5 0 1 1 12 6.5a2.5 2.5 0 0 1 0 5z"/></svg>24 Larchmont Rise, Halden Vale</li>
      <li><svg width="8" height="8" viewBox="0 0 24 24"><path fill="#a9a9a9" d="M6.6 10.8a15 15 0 0 0 6.6 6.6l2.2-2.2c.3-.3.7-.4 1-.2 1.1.4 2.3.6 3.6.6.6 0 1 .4 1 1V20c0 .6-.4 1-1 1A17 17 0 0 1 3 4c0-.6.4-1 1-1h3.5c.6 0 1 .4 1 1 0 1.3.2 2.5.6 3.6.1.3 0 .7-.2 1z"/></svg>555-014-7720</li>
      <li><svg width="9" height="7" viewBox="0 0 24 18"><rect x="1" y="1" width="22" height="16" fill="none" stroke="#a9a9a9" stroke-width="2"/><path d="M1 1l11 9 11-9" fill="none" stroke="#a9a9a9" stroke-width="2"/></svg>studio@haldencrest.example</li>
    </ul>
  </div>
  <div class="footer-col fc-map">
    <h4>Contact Information</h4>
    <div class="map" role="img" aria-label="Street map showing the studio location"></div>
  </div>
  <div class="footer-col fc-follow">
    <h4>Follow Us</h4>
    <ul>
      <li><span class="social-square"></span>Social feed</li>
      <li><span class="social-square"></span>Photo journal</li>
      <li><span class="social-square"></span>Studio news</li>
    </ul>
  </div>
</footer>
<div class="copyright">© 2024 Halden Crest Studio. All rights reserved.</div>

</body>
</html>
```